Broschüre für Personaldienstleister
Zielgruppe
Wir sind ein Personaldienstleister und vermitteln ausländisches medizinisches Fachpersonal an deutsche Einrichtungen. Unsere Zielgruppe sind Krankenhäuser, Pflegeheime, Ärztehäuser, Praxen, Labore und weitere medizinische Institutionen.
Aufgabenstellung
Wir haben eine Infobroschüre sowie eine PowerPoint Präsentation bereits mit einem groben Design erstellt. Texte und Beispielbilder (Stockmaterial) sind ebenfalls vorhanden, gerne wünschen wir uns auch Eigeninitiative bei der Wahl der Bilder passend zum neuen Design.
Wir wünschen uns ein Redesign mit einem kreativen, einzigartigen Design. Zudem ist uns wichtig, dass unsere Infografiken qualitativ und hochwertig gestaltet werden.
Dieses Projekt ist mit zukünftigen Folgeprojekten verbunden, da wir weitere Präsentationen und Broschüren für andere Zielgruppen benötigen.

```html
<!DOCTYPE html>
<html lang="de">
<head>
<meta charset="utf-8">
<title>Kalvora HR – Broschüre</title>
<link rel="stylesheet" href="https://fonts.googleapis.com/css2?family=Montserrat:wght@500;600;700;800&family=Roboto:wght@400;500&display=swap">
<style>
  :root{
    --bg:#d9d9d9;
    --paper:#f2f2f2;
    --paper-edge:#e2e2e2;
    --ink:#3a3a3a;
    --teal-dark:#1c4446;
    --teal:#2a5a5b;
    --green:#2f7c63;
    --green-light:#5d9c84;
    --green-pale:#8fb9a5;
    --slate:#22474b;
    --black:#0b0b0b;
    --white:#ffffff;
    --chalk:#c8c8c8;
    --skin:#d9a58a;
  }
  *{margin:0;padding:0;box-sizing:border-box}
  html,body{width:1200px;height:826px;overflow:hidden;background:var(--bg)}
  .spread{position:absolute;left:40px;top:17px;width:1120px;height:792px;display:flex;box-shadow:0 10px 30px rgba(0,0,0,.25)}
  .page{position:relative;width:560px;height:792px;overflow:hidden}

  /* left page */
  .page--left{background:linear-gradient(90deg,var(--paper) 0%,var(--paper) 85%,var(--paper-edge) 100%);font-family:"Roboto",sans-serif;color:var(--ink)}
  .hero-blob{position:absolute;left:10px;top:170px;width:190px;height:110px;border-radius:50%;background:var(--green-pale);opacity:.7;transform:rotate(-12deg)}
  .hero-photo{position:absolute;left:22px;top:38px;width:200px;height:200px;border-radius:50%;border:6px solid var(--teal-dark);background:radial-gradient(circle at 45% 55%,var(--skin) 0%,#3aa38f 35%,#1d8c7a 70%,#1a6f62 100%)}
  .banner{position:absolute;font-family:"Montserrat",sans-serif;font-weight:600;color:var(--white);display:flex;align-items:center;padding-left:22px}
  .banner--question{left:200px;top:64px;width:220px;height:34px;background:var(--teal);font-size:14px}
  .banner--answer{left:200px;top:100px;width:290px;height:32px;background:var(--green-light);font-size:13px}
  .body-copy{position:absolute;left:36px;top:282px;width:486px;font-size:10px;line-height:1.42;text-align:justify;letter-spacing:.1px}
  .footer-band{position:absolute;left:0;bottom:0;width:560px;height:44px;background:var(--teal-dark);display:flex;justify-content:space-around;align-items:center;font-family:"Montserrat",sans-serif;font-size:10px;color:var(--white);letter-spacing:.3px}

  /* right page */
  .page--right{background:var(--black);font-family:"Roboto",sans-serif;color:var(--white)}
  .page-title{position:absolute;left:46px;top:58px;font-family:"Montserrat",sans-serif;font-weight:700;font-size:25px;letter-spacing:.3px;color:#f1f1f1}
  .infographic{position:absolute;left:0;top:0}
  .infographic text{font-family:"Roboto",sans-serif;font-size:6.6px;fill:#e8e8e8}
  .chalk-numeral{position:absolute;left:150px;top:570px;width:250px;height:150px;background:linear-gradient(135deg,#3a3a3a,#1e1e1e);border-radius:6px}
  .hand-photo{position:absolute;left:400px;top:500px;width:150px;height:200px;border-radius:40px 40px 10px 10px;background:radial-gradient(circle at 35% 30%,#e4e03a 0%,#c9b436 18%,var(--skin) 40%,#9b6b55 100%)}
</style>
</head>
<body>
<div class="spread">
  <section class="page page--left">
    <div class="hero-blob"></div>
    <div class="hero-photo" role="img" aria-label="Foto: Pflegekräfte in grüner Kleidung legen die Hände übereinander"></div>
    <div class="banner banner--question">Haben wir Sie überzeugt?</div>
    <div class="banner banner--answer">Dann gehen Sie den Weg mit uns!</div>
    <p class="body-copy">
      Wir von Kalvora bieten Ihnen als spezialisierte Personalvermittlung qualifizierte Pflege- und Gesundheitsfachkräfte aus der Türkei zu besten Konditionen. Als Experte im Rekrutieren von Personal aus der Türkei stellen wir Ihnen ein breites Spektrum an medizinischem Fachpersonal zur Verfügung. Unser Rekrutierungs-Team in der Türkei findet Fachkräfte, die optimal zu Ihrem Unternehmen passen und unser HR-Spezialisten in Deutschland übernehmen die weitere Organisation mit unserem 360°-Service.<br>
      Wir begleiten das gesamte Bewerbungsverfahren und kümmern uns sowohl um die Kommunikation als auch um den Transfer Ihrer neuen Mitarbeiter:innen. Auch nach Ankunft sind wir stets an Ihrer Seite und unterstützen Sie aktiv vor Ort bei der Integration. Unsere zweisprachigen Kolleg:innen in Deutschland und der Türkei sorgen für reibungslose Abläufe und eine einfache Kommunikation zwischen den Parteien.<br>
      Durch unsere spezialisierte Expertise im Personalwesen bekommen Sie keine Dienstleistung von der Stange, sondern wir schneidern eine passgenaue Personallösung nur für Sie – maßgeschneidert eben! Dabei legen wir großen Wert auf einen transparenten, offenen und kultursensiblen Umgang. Und das bezieht sich nicht nur auf unsere Mitarbeiter:innen, weshalb auch unsere Kooperationseinrichtungen uns als HR-Spezialisten in Personalfragen vertrauen. Wir sind ein verlässlicher Begleiter auf Ihrem Weg zur neuen Fachkraft und erst dann zufrieden, wenn Sie es sind. Stellen Sie noch heute die Weichen, um eine nachhaltige Grundversorgung im Gesundheitswesen für morgen sicherzustellen. Sparen Sie Zeit und Ressourcen bei der Personalsuche, indem Sie unsere Expert:innen mit dieser Aufgabe betrauen.<br>
      Wir bei Kalvora HR freuen uns, mit Ihnen als Partner zukünftig neue Wege zu bestreiten.
    </p>
    <footer class="footer-band">
      <span>+49 000 123 45 678</span>
      <span>hr@kalvora.com</span>
      <span>www.kalvora-hr.com</span>
    </footer>
  </section>

  <section class="page page--right">
    <h2 class="page-title">Unser 360°-Service auf einem Blick</h2>
    <svg class="infographic" width="560" height="792" viewBox="0 0 560 792">
      <g transform="rotate(-90 280 330)" fill="none" stroke-width="54">
        <circle cx="280" cy="330" r="86" stroke="#2f7c63" stroke-dasharray="54.04 486.3" stroke-dashoffset="0"/>
        <circle cx="280" cy="330" r="86" stroke="#1f4e50" stroke-dasharray="54.04 486.3" stroke-dashoffset="-54.04"/>
        <circle cx="280" cy="330" r="86" stroke="#3f8a72" stroke-dasharray="54.04 486.3" stroke-dashoffset="-108.08"/>
        <circle cx="280" cy="330" r="86" stroke="#173c3d" stroke-dasharray="54.04 486.3" stroke-dashoffset="-162.12"/>
        <circle cx="280" cy="330" r="86" stroke="#2f7c63" stroke-dasharray="54.04 486.3" stroke-dashoffset="-216.16"/>
        <circle cx="280" cy="330" r="86" stroke="#183e40" stroke-dasharray="54.04 486.3" stroke-dashoffset="-270.2"/>
        <circle cx="280" cy="330" r="86" stroke="#2a7360" stroke-dasharray="54.04 486.3" stroke-dashoffset="-324.24"/>
        <circle cx="280" cy="330" r="86" stroke="#16393b" stroke-dasharray="54.04 486.3" stroke-dashoffset="-378.28"/>
        <circle cx="280" cy="330" r="86" stroke="#2e7a64" stroke-dasharray="54.04 486.3" stroke-dashoffset="-432.32"/>
        <circle cx="280" cy="330" r="86" stroke="#163c3c" stroke-dasharray="54.04 486.3" stroke-dashoffset="-486.36"/>
      </g>
      <circle cx="280" cy="330" r="58" fill="#e9ecea"/>
      <circle cx="280" cy="330" r="48" fill="#b9cdc4"/>
      <text x="280" y="343" text-anchor="middle" style="font-family:'Montserrat',sans-serif;font-weight:800;font-size:34px;fill:#2a6e5c">360°</text>

      <g stroke="#d0d0d0" stroke-width=".8" stroke-dasharray="3 2" fill="none">
        <polyline points="305,222 310,190 395,186"/>
        <polyline points="360,262 405,258"/>
        <polyline points="392,340 418,338"/>
        <polyline points="355,408 370,428 418,426"/>
        <polyline points="300,444 304,466"/>
        <polyline points="225,440 220,462 120,478"/>
        <polyline points="185,404 120,412"/>
        <polyline points="168,332 120,338"/>
        <polyline points="170,290 120,284"/>
        <polyline points="232,226 215,208 145,210"/>
      </g>

      <text x="400" y="184">Großer Bewerberpool an</text>
      <text x="400" y="192">türkischen Fachkräften</text>
      <text x="410" y="254">Innovatives Recruiting mit</text>
      <text x="410" y="262">schnellen Ergebnissen auf</text>
      <text x="410" y="270">allen Kanälen</text>
      <text x="422" y="330">Passgenaue Lösungen</text>
      <text x="422" y="338">individuell auf Ihre Bedürfnisse</text>
      <text x="422" y="346">zugeschnitten</text>
      <text x="422" y="418">Transparentes Auswahlverfahren</text>
      <text x="422" y="426">von der ersten Kontaktaufnahme</text>
      <text x="422" y="434">bis hin zum Vertragsabschluss</text>
      <text x="262" y="478">Persönliches Begleiten der</text>
      <text x="262" y="486">Vorstellungsgespräche</text>
      <text x="40" y="478">Exklusive, eigens für Sie</text>
      <text x="40" y="486">durchgeführte Rekruti-</text>
      <text x="40" y="494">erungskampagnen</text>
      <text x="40" y="404">Übernahme der</text>
      <text x="40" y="412">Abschlussgespräche,</text>
      <text x="40" y="420">sowie der Korrespon-</text>
      <text x="40" y="428">denz mit den beteiligten</text>
      <text x="40" y="436">Bewerbern</text>
      <text x="40" y="330">Nachhaltige</text>
      <text x="40" y="338">Steigerung der</text>
      <text x="40" y="346">Performance Ihrer</text>
      <text x="40" y="354">Einrichtung</text>
      <text x="30" y="280">Professionelle Vorauswahl an</text>
      <text x="30" y="288">qualifizierten Kandidat:innen</text>
      <text x="40" y="208">Expert:innen mit interkulturellem</text>
      <text x="40" y="216">Know-How</text>
    </svg>
    <div class="chalk-numeral" role="img" aria-label="Handgezeichnete Kreideschrift „360°“"></div>
    <div class="hand-photo" role="img" aria-label="Foto: Hand zeichnet einen gelben Kreispfeil mit Kreide"></div>
  </section>
</div>
</body>
</html>
```